GJ & DW Fencing Pty Ltd

We already have an existing logo created by Pixel Harbour however we have restructured to a company. We would like someone to add Pty Ltd to our business name please.

Colors

Designer to choose only greyscale colors for use in the design.

```html
<!DOCTYPE html>
<html lang="en">
<head>
<meta charset="utf-8">
<title>GJ &amp; DW Fencing Pty Ltd — Business Card</title>
<link href="https://fonts.googleapis.com/css2?family=Merriweather:wght@700&family=Lato:wght@400&display=swap" rel="stylesheet">
<style>
  :root {
    --backdrop: #3b3836;
    --card: #0e0e0e;
    --ink: #f2f2f2;
    --ink-soft: #c9c9c9;
    --rule: #3a3a3a;
  }
  * { margin: 0; padding: 0; box-sizing: border-box; }
  html, body { width: 1200px; height: 844px; overflow: hidden; }
  body {
    background: var(--backdrop);
    display: flex;
    align-items: center;
    justify-content: center;
    gap: 48px;
    font-family: "Lato", sans-serif;
  }
  .card {
    width: 520px;
    height: 318px;
    background: var(--card);
    box-shadow: 0 18px 40px rgba(0,0,0,0.45);
    position: relative;
    color: var(--ink);
  }
  .wordmark {
    font-family: "Merriweather", serif;
    font-weight: 700;
    color: var(--ink);
    display: flex;
    align-items: center;
    gap: 10px;
    line-height: 1.1;
  }
  .wordmark-dot {
    width: 14px; height: 14px; border-radius: 50%;
    background: var(--ink); flex: none;
  }
  .card-front { display: flex; align-items: center; }
  .card-front .brand {
    width: 52%;
    display: flex; justify-content: center;
  }
  .card-front .wordmark { font-size: 19px; }
  .card-front .divider {
    width: 1px; height: 150px; background: var(--rule);
  }
  .contact { padding-left: 26px; }
  .contact-name {
    font-family: "Merriweather", serif;
    font-weight: 700;
    font-size: 14px;
    letter-spacing: 0.06em;
    text-transform: uppercase;
    margin-bottom: 12px;
  }
  .contact-list { list-style: none; }
  .contact-list li {
    display: flex; align-items: center; gap: 8px;
    font-size: 12.5px; color: var(--ink-soft);
    margin-bottom: 7px;
  }
  .contact-list svg { width: 12px; height: 12px; fill: var(--ink); flex: none; }
  .card-back { display: flex; align-items: center; justify-content: center; }
  .card-back .wordmark { font-size: 26px; }
</style>
</head>
<body>
  <section class="card card-front">
    <div class="brand">
      <div class="wordmark"><span class="wordmark-dot"></span>GJ &amp; DW Fencing<br>Pty Ltd</div>
    </div>
    <div class="divider"></div>
    <div class="contact">
      <p class="contact-name">Ray Tallis</p>
      <ul class="contact-list">
        <li><svg viewBox="0 0 24 24"><path d="M6.6 10.8a15 15 0 0 0 6.6 6.6l2.2-2.2a1 1 0 0 1 1-.25 11.4 11.4 0 0 0 3.6.57 1 1 0 0 1 1 1V20a1 1 0 0 1-1 1A17 17 0 0 1 3 4a1 1 0 0 1 1-1h3.5a1 1 0 0 1 1 1c0 1.25.2 2.45.57 3.6a1 1 0 0 1-.25 1z"/></svg>044 5182907</li>
        <li><svg viewBox="0 0 24 24"><path d="M2 5h20v14H2z M2 5l10 8 10-8" fill="none" stroke="#f2f2f2" stroke-width="2"/></svg>gjdwfencing@mailbox.com</li>
        <li><svg viewBox="0 0 24 24"><path d="M12 2a7 7 0 0 0-7 7c0 5.2 7 13 7 13s7-7.8 7-13a7 7 0 0 0-7-7zm0 9.5A2.5 2.5 0 1 1 12 6.5a2.5 2.5 0 0 1 0 5z"/></svg>PO Box 418 Kelmscott WA 6111</li>
      </ul>
    </div>
  </section>
  <section class="card card-back">
    <div class="wordmark"><span class="wordmark-dot"></span>GJ &amp; DW Fencing<br>Pty Ltd</div>
  </section>
</body>
</html>
```